Business Card Design Project

We have recently completed CraftHive projects for a new logo and wesbite.
We now require new business cards.
We hand out very little printed material to clients as all information is online. When we do hand out something, like a business card, we want it to have real impact and make a statement about the quality and professionalism of our company.
We have an idea of what we want our card to look like but we want a designer to make sure they have impact and look great.
Our requirements are…
Size: 85mm X 55mm - Landscape
Front of card: Logo plus the following contact information.
Dennis Marlow
Operations Manager
Phone +44(0) 1632 xxx xxx
Mobile +44(0) 7700 xxx xxx
Email denmo@korvantix.example
Address 17 Pellick Row, Aberdeen AB12 9QZ
Website www.korvantix.example
How you layout the front of the card is up to you, we would like to see some different ideas. Attached are two versions of our logo that may be used.
Back of card: We would like this to be simple but again have impact. Our current thought is to have the logo or just the large W design from the logo in white against a dark background, perhaps made up from the dark green in the logo.
The logos are attached so you can see the colours in them but the dark ones are..
Dark Blue = C:88, M:55, Y:44, K:28
Dark Green = C:87, M:53, Y:50, K:50
We sometimes also use a bright orange as an accent or highlight colour…
Orange: = C:0, M:39, Y:94, K:0

```html
<!DOCTYPE html>
<html lang="en">
<head>
<meta charset="utf-8">
<title>Korvantix Business Cards</title>
<link rel="stylesheet" href="https://fonts.googleapis.com/css2?family=Montserrat:wght@600;700&family=Questrial&display=swap">
<style>
  :root {
    --backdrop: #e7e4df;
    --card: #ffffff;
    --ink: #1f1f1f;
    --teal-dark: #1d4450;
    --teal-deep: #163f47;
    --teal-mid: #2f5f6b;
    --teal-light: #7db8bd;
    --olive: #8a9a4a;
    --text: #3a3a3a;
    --band-text: #ffffff;
  }
  * { box-sizing: border-box; margin: 0; padding: 0; }
  html, body { width: 1200px; height: 788px; overflow: hidden; }
  body {
    position: relative;
    background: var(--backdrop);
    font-family: "Questrial", "Century Gothic", sans-serif;
    color: var(--text);
  }
  .view-label {
    position: absolute;
    width: 502px;
    text-align: center;
    font-size: 22px;
    color: var(--ink);
  }
  .card {
    position: absolute;
    width: 502px;
    height: 325px;
    border-radius: 18px;
    background: var(--card);
    overflow: hidden;
  }
  .card--front { left: 66px; top: 52px; }
  .card--back-1 { left: 626px; top: 53px; }
  .card--back-2 { left: 66px; top: 443px; background: var(--teal-deep); }
  .card--back-3 { left: 626px; top: 443px; }

  .brand {
    position: absolute;
    display: flex;
    align-items: center;
    gap: 10px;
  }
  .brand__dot {
    border-radius: 50%;
    background: var(--teal-mid);
    flex: none;
  }
  .brand__name {
    font-family: "Montserrat", "Arial", sans-serif;
    font-weight: 700;
    color: var(--teal-dark);
    letter-spacing: 0.5px;
  }

  .card--front .brand { left: 28px; top: 142px; }
  .card--front .brand__dot { width: 26px; height: 26px; }
  .card--front .brand__name { font-size: 27px; }

  .divider {
    position: absolute;
    left: 250px;
    top: 108px;
    width: 2px;
    height: 118px;
    background: linear-gradient(to bottom, rgba(60,60,60,0), #555 50%, rgba(60,60,60,0));
  }
  .contact {
    position: absolute;
    left: 273px;
    top: 107px;
    list-style: none;
    font-size: 13px;
    line-height: 23.5px;
  }
  .contact li { display: flex; align-items: flex-start; gap: 7px; }
  .contact svg { width: 11px; height: 11px; margin-top: 6px; flex: none; fill: var(--teal-dark); }
  .contact .address { line-height: 17px; padding-top: 3px; }

  .name-band {
    position: absolute;
    left: 0; bottom: 0;
    width: 100%;
    height: 38px;
    background: var(--teal-dark);
    color: var(--band-text);
    display: flex;
    align-items: center;
    justify-content: center;
    gap: 5px;
  }
  .name-band__name { font-family: "Montserrat", "Arial", sans-serif; font-weight: 700; font-size: 15px; }
  .name-band__role { font-size: 13px; }

  .card--back-1 .brand { left: 0; width: 100%; justify-content: center; top: 108px; }
  .card--back-1 .brand__dot { width: 44px; height: 44px; }
  .card--back-1 .brand__name { font-size: 40px; }

  .card--back-2 .brand { left: 0; width: 100%; justify-content: center; top: 136px; }
  .card--back-2 .brand__dot { width: 48px; height: 48px; background: var(--teal-light); opacity: 0.55; }
  .card--back-2 .brand__name { font-size: 44px; color: var(--teal-light); opacity: 0.55; }

  .card--back-3 .brand { left: 0; width: 100%; justify-content: center; top: 150px; }
  .card--back-3 .brand__dot { width: 52px; height: 52px; }
  .card--back-3 .brand__name { font-size: 48px; }

  .web {
    position: absolute;
    left: 0; width: 100%;
    text-align: center;
    font-size: 18px;
    letter-spacing: 3px;
    color: var(--teal-dark);
  }
  .card--back-1 .web { top: 285px; }
  .card--back-3 .web { top: 281px; }
</style>
</head>
<body>
  <div class="view-label" style="left:66px; top:19px;">Front</div>
  <div class="view-label" style="left:626px; top:19px;">Back - 1</div>
  <div class="view-label" style="left:66px; top:402px;">Back - 2</div>
  <div class="view-label" style="left:626px; top:402px;">Back - 3</div>

  <section class="card card--front" aria-label="Card front">
    <div class="brand"><span class="brand__dot"></span><span class="brand__name">KORVANTIX</span></div>
    <div class="divider"></div>
    <ul class="contact">
      <li><svg viewBox="0 0 12 12" aria-hidden="true"><rect x="3" y="0.5" width="6" height="11" rx="1.2"/></svg>+44(0) 7700 xxx xxx</li>
      <li><svg viewBox="0 0 12 12" aria-hidden="true"><path d="M2 1l3 0 1 3-1.5 1a7 7 0 0 0 3.5 3.5L9 7l3 1v3c-6 0-10-4-10-10z"/></svg>+44(0) 1632 xxx xxx</li>
      <li><svg viewBox="0 0 12 12" aria-hidden="true"><path d="M0 2h12v8H0z M1 3l5 3.5L11 3" stroke="#fff" stroke-width="1"/></svg>denmo@korvantix.example</li>
      <li><svg viewBox="0 0 12 12" aria-hidden="true"><circle cx="6" cy="6" r="5.5"/></svg>www.korvantix.example</li>
      <li><svg viewBox="0 0 12 12" aria-hidden="true"><path d="M6 0.5L0 6h2v5.5h3V8h2v3.5h3V6h2z"/></svg><span class="address">17 Pellick Row<br>Aberdeen AB12 9QZ</span></li>
    </ul>
    <div class="name-band"><span class="name-band__name">Dennis Marlow,</span><span class="name-band__role">Operations Manager</span></div>
  </section>

  <section class="card card--back-1" aria-label="Card back, option 1">
    <div class="brand"><span class="brand__dot"></span><span class="brand__name">KORVANTIX</span></div>
    <p class="web">www.korvantix.example</p>
  </section>

  <section class="card card--back-2" aria-label="Card back, option 2">
    <div class="brand"><span class="brand__dot"></span><span class="brand__name">KORVANTIX</span></div>
  </section>

  <section class="card card--back-3" aria-label="Card back, option 3">
    <div class="brand"><span class="brand__dot"></span><span class="brand__name">KORVANTIX</span></div>
    <p class="web">www.korvantix.example</p>
  </section>
</body>
</html>
```